Fitness Equipment Repair Business Needs a Catchy New Business Card

We have an existing business card, however, it is quite plain and boring. We are expanding primarily in the commercial area (gyms, studios, apartment complexes etc). The business card will serve as eye candy to those managers/owners that can't be met for a face to face.
Originally I was planning for a brochure as well, but all of our information is better summarized on our website. (brightloopservice.ca).
I would like the card to match the colour scheme of the website and utilize the logo. It should have a professional clean feel to it, however, a little colouring outside the lines wouldn't hurt.
The example card is for my service technician (Colin Marsh). If possible I would like to be able to edit the text to use for more than one person.

Industry/Entity Type

Appliance Repair

Contact Information for Business Card

Clean, crisp and professional but needs to be eye catching. Preferably using the black, white and red colour scheme matching the website. Double sided would be nice, but is not necessary.

Colors
ec1f27
ffffff
000000

Requirements
Must have
• Must be able to edit name, phone number and title to use for multiple people. Must show the company website (brightloopservice.ca).

```html
<!DOCTYPE html>
<html lang="en">
<head>
<meta charset="utf-8">
<title>Bright Loop Service – Business Card</title>
<link href="https://fonts.googleapis.com/css2?family=Arimo:wght@400&family=Montserrat:wght@500;700&display=swap" rel="stylesheet">
<style>
  :root {
    --red: #ec1f27;
    --black: #000000;
    --white: #ffffff;
    --backdrop: #dcd8d3;
    --shade: #1c1c1c;
  }
  html, body {
    margin: 0;
    padding: 0;
    width: 1200px;
    height: 987px;
    overflow: hidden;
    background: var(--backdrop);
  }
  .canvas {
    position: relative;
    width: 1200px;
    height: 987px;
  }

  /* Front: vertical card */
  .card-front {
    position: absolute;
    left: 131px;
    top: 173px;
    width: 352px;
    height: 616px;
    background: var(--black);
    box-shadow: 0 4px 14px rgba(0,0,0,.35);
    overflow: hidden;
  }
  .card-front .red-panel {
    position: absolute;
    left: 0;
    top: 0;
    width: 352px;
    height: 616px;
  }
  .card-front .mark {
    position: absolute;
    left: 106px;
    top: 90px;
    width: 140px;
    height: 140px;
    box-sizing: border-box;
    border: 3px solid var(--white);
    border-radius: 50%;
  }
  .contact {
    position: absolute;
    left: 0;
    width: 352px;
    top: 354px;
    text-align: center;
    color: var(--white);
    font-family: "Arimo", sans-serif;
  }
  .contact .name {
    font-family: "Montserrat", sans-serif;
    font-weight: 700;
    font-variant: small-caps;
    letter-spacing: 1.5px;
    font-size: 24px;
    line-height: 26px;
    margin: 0;
  }
  .contact .title {
    font-family: "Montserrat", sans-serif;
    font-weight: 500;
    font-variant: small-caps;
    letter-spacing: 1.2px;
    font-size: 17px;
    line-height: 22px;
    margin: 2px 0 0;
  }
  .contact .address {
    font-size: 16px;
    line-height: 22px;
    margin: 14px 0 0;
  }
  .contact .lines {
    font-size: 16px;
    line-height: 23.5px;
    margin: 16px 0 0;
  }
  .contact .label { font-weight: 700; }

  /* Back: horizontal card */
  .card-back {
    position: absolute;
    left: 498px;
    top: 437px;
    width: 615px;
    height: 351px;
    background: var(--black);
    box-shadow: 0 4px 14px rgba(0,0,0,.35);
    overflow: hidden;
  }
  .card-back .stripe {
    position: absolute;
    left: 0;
    bottom: 0;
    width: 100%;
    height: 8px;
    background: var(--red);
  }
  .card-back .mark {
    position: absolute;
    left: 78px;
    top: 100px;
    width: 86px;
    height: 86px;
    box-sizing: border-box;
    border: 2px solid var(--white);
    border-radius: 50%;
  }
  .card-back .initials {
    position: absolute;
    left: 70px;
    top: 220px;
    width: 102px;
    text-align: center;
    font-family: "Montserrat", sans-serif;
    font-weight: 700;
    font-size: 28px;
    letter-spacing: 1px;
    color: var(--red);
  }
  .card-back .company {
    position: absolute;
    left: 235px;
    top: 158px;
    font-family: "Montserrat", sans-serif;
    font-weight: 700;
    font-variant: small-caps;
    letter-spacing: 1.5px;
    font-size: 20px;
    color: var(--white);
  }
</style>
</head>
<body>
<div class="canvas">

  <section class="card-front">
    <svg class="red-panel" width="352" height="616" viewBox="0 0 352 616" aria-hidden="true">
      <polygon fill="var(--red)" points="0,333 74,333 84,322 250,322 262,333 352,333 352,616 0,616"/>
    </svg>
    <div class="mark" aria-hidden="true"></div>
    <div class="contact">
      <p class="name">Colin Marsh</p>
      <p class="title">Service technician</p>
      <p class="address">1875 Larkfield Road NW<br>Edmonton AB T5K 2P4</p>
      <p class="lines">
        <span class="label">P :</span> 587-555-0142<br>
        <span class="label">P :</span> 780-555-0187<br>
        <span class="label">E :</span> service@brightloopservice.ca<br>
        www.brightloopservice.ca
      </p>
    </div>
  </section>

  <section class="card-back">
    <div class="mark" aria-hidden="true"></div>
    <div class="initials">BLS</div>
    <div class="company">Bright Loop Service</div>
    <div class="stripe"></div>
  </section>

</div>
</body>
</html>
```